Logo & Visitenkarte für Weinbauer
Zielgruppe
Ich bin Weinbauer und betreibe auch einen Buschenschank. Zielgruppe ist die Gastronomie und der (Durchschnitts-) Endverbraucher.
Aufgabenstellung
Unsere Betriebsstätte ist im Rebhügelgau Weinviertel (Österreich).
Wir wollen die Werte Tradition, Regional, Vertrauen und Bodenständigkeit vermitteln.
Unsere Kunden schätzen die Herkunft.
Das Logo soll als Firmenlogo und auch für die Weinetiketten verwendet werden können.

```html
<!DOCTYPE html>
<html lang="de">
<head>
<meta charset="utf-8">
<title>Weinbau Brunner – Etikett</title>
<link href="https://fonts.googleapis.com/css2?family=Oswald:wght@400&family=Open+Sans:wght@700&display=swap" rel="stylesheet">
<style>
  :root {
    --backdrop: #1c1213;
    --gold-light: #e2c4a2;
    --gold-mid: #c9a27c;
    --gold-deep: #a98060;
    --ink: #1f1a17;
  }
  html, body {
    margin: 0;
    padding: 0;
    width: 1164px;
    height: 1200px;
    overflow: hidden;
    background: var(--backdrop);
  }
  .label-canvas {
    position: relative;
    width: 1164px;
    height: 1200px;
  }
  .label-shapes {
    position: absolute;
    inset: 0;
  }
  .brand-name {
    position: absolute;
    left: 0;
    width: 1164px;
    top: 622px;
    margin: 0;
    text-align: center;
    font-family: "Oswald", sans-serif;
    font-weight: 400;
    font-size: 40px;
    letter-spacing: 1px;
    color: var(--ink);
  }
  .label-copy {
    position: absolute;
    left: 437px;
    width: 290px;
    top: 792px;
    margin: 0;
    text-align: center;
    font-family: "Open Sans", sans-serif;
    font-weight: 700;
    font-size: 11.5px;
    line-height: 14px;
    color: var(--ink);
  }
</style>
</head>
<body>
<main class="label-canvas">
  <svg class="label-shapes" width="1164" height="1200" viewBox="0 0 1164 1200" xmlns="http://www.w3.org/2000/svg">
    <defs>
      <linearGradient id="goldFoil" x1="0" y1="0" x2="1" y2="1">
        <stop offset="0" stop-color="var(--gold-light)"/>
        <stop offset="0.45" stop-color="var(--gold-mid)"/>
        <stop offset="0.75" stop-color="var(--gold-light)"/>
        <stop offset="1" stop-color="var(--gold-deep)"/>
      </linearGradient>
    </defs>

    <!-- decorative rings -->
    <g class="deco-rings" fill="none" stroke="url(#goldFoil)" stroke-width="6">
      <circle cx="632" cy="60" r="36"/>
      <circle cx="782" cy="160" r="80"/>
      <circle cx="332" cy="975" r="80"/>
    </g>

    <!-- label body: side band + pill -->
    <g class="label-body" fill="url(#goldFoil)">
      <rect x="348" y="360" width="468" height="500" rx="20"/>
      <rect x="372" y="210" width="420" height="780" rx="210"/>
    </g>

    <!-- inner frame lines -->
    <g class="label-frame" fill="none" stroke="var(--ink)" stroke-width="2.5">
      <rect x="388" y="226" width="388" height="748" rx="194"/>
      <path d="M 420 880 A 170 170 0 0 0 744 880"/>
    </g>

    <!-- brand mark placeholder -->
    <circle class="brand-dot" cx="582" cy="570" r="36" fill="none" stroke="var(--ink)" stroke-width="3"/>
  </svg>

  <h1 class="brand-name">WEINBAU BRUNNER</h1>

  <p class="label-copy">Unsere Weine wachsen auf sanften Hügeln im Rebhügelgau, gepflegt mit viel Handarbeit und Geduld. Seit Generationen keltern wir im eigenen Keller, schenken im Buschenschank aus und teilen die Freude am Wein mit Gästen aus nah und fern. Jede Flasche erzählt von Boden, Sonne und Herkunft. Zum Wohl aus dem Weingut der Familie Brunner.</p>
</main>
</body>
</html>
```